Brightfield Ventures Inc. Letterhead

Creation of attractive and eye catching letterhead for a business start-up for the construction industry. Letterhead must relate to construction, but avoid standard hammer and tools in the design.

I forgot to add some details, sorry about that. Some pertinent info: Ph: 916-555-0187 brightfieldventures.example 448 Willowmere Ave, Ste 210 Folsom, CA 95999 info@brightfieldventures.example not sure if slogan should be in there" “Connecting construction professionals to create a purpose driven industry.” must be able to be used in word. Thanks!

```html
<!DOCTYPE html>
<html lang="en">
<head>
<meta charset="utf-8">
<title>Brightfield Ventures Inc. Letterhead</title>
<link href="https://fonts.googleapis.com/css2?family=Lato:wght@400;700&family=Kaushan+Script&display=swap" rel="stylesheet">
<style>
  :root {
    --navy: #1c2354;
    --red: #c8202f;
    --body: #4d4d4f;
    --paper: #ffffff;
    --footer-text: #4a4a4a;
  }
  * { box-sizing: border-box; margin: 0; padding: 0; }
  html, body { width: 957px; height: 1200px; overflow: hidden; background: var(--paper); }
  .letterhead {
    position: relative;
    width: 957px;
    height: 1200px;
    background: var(--paper);
    font-family: "Lato", sans-serif;
    color: var(--body);
  }
  .brand {
    position: absolute;
    top: 44px;
    left: 0;
    width: 100%;
    display: flex;
    flex-direction: column;
    align-items: center;
    gap: 16px;
  }
  .brand-square { width: 34px; height: 34px; background: var(--red); }
  .brand-name {
    font-weight: 700;
    font-size: 24px;
    letter-spacing: 3px;
    color: var(--navy);
    text-transform: uppercase;
  }
  .letter {
    position: absolute;
    top: 230px;
    left: 82px;
    width: 794px;
  }
  .salutation {
    font-weight: 700;
    font-size: 18px;
    color: var(--navy);
    margin-bottom: 20px;
  }
  .letter-body p {
    font-size: 18px;
    line-height: 28px;
    text-align: justify;
    hyphens: auto;
    margin-bottom: 20px;
  }
  .closing {
    margin-top: 30px;
    font-size: 21px;
    color: #2a2a2a;
  }
  .signature {
    font-family: "Kaushan Script", cursive;
    font-size: 34px;
    color: var(--navy);
    margin-top: 6px;
  }
  .contact {
    position: absolute;
    bottom: 20px;
    left: 0;
    width: 100%;
    text-align: center;
    font-size: 14px;
    color: var(--footer-text);
  }
  .contact-row {
    display: flex;
    justify-content: center;
    gap: 12px;
    margin-top: 8px;
  }
  .contact-item { display: inline-flex; align-items: center; gap: 4px; }
  .contact-item svg { width: 12px; height: 12px; fill: none; stroke: var(--red); stroke-width: 2; }
</style>
</head>
<body>
<div class="letterhead">
  <header class="brand">
    <div class="brand-square"></div>
    <div class="brand-name">Brightfield Ventures</div>
  </header>

  <main class="letter">
    <p class="salutation">Dear Mr. Lorem,</p>
    <div class="letter-body">
      <p>Lorem ipsum dolor sit amet, consectetuer adipiscing elit, sed diam nonummy nibh euismod tincidunt ut laoreet dolore magna aliquam erat volutpat. Ut wisi enim ad minim veniam, quis nostrud exerci tation ullamcorper suscipit lobortis nisl ut aliquip ex ea commodo consequat. Duis autem vel eum iriure dolor in hendiusto odio dignissim qui blandit praesent luptatum zzril delenit augue duis dolore te feugait nulla facilisi.</p>
      <p>Lorem ipsum dolor sit amet, consectetuer adipiscing elit, sed diam nonummy nibh euismod tincidunt ut laoreet dolore magna aliquam erat volutpat. Ut wisi enim ad minim veniam, quis nostrud exerci tation ullamcorper suscipit lobortis nisl ut aliquip ex ea commodo consequat. Duis autem vel eum iriure dolor in hendiusto odio dignissim qui blandit praesent luptatum zzril delenit augue duis dolore te feugait nulla facilisi.</p>
      <p>Lorem ipsum dolor sit amet, consectetuer adipiscing elit, sed diam nonummy nibh euismod tincidunt ut laoreet dolore magna aliquam erat volutpat. Ut wisi enim ad minim veniam, quis nostrud exerci tation ullamcorper suscipit lobortis nisl ut aliquip ex ea commodo consequat. Duis autem vel eum iriure dolor in hendiusto odio dignissim qui blandit praesent luptatum zzril delenit augue duis dolore te feugait nulla facilisi.</p>
    </div>
    <p class="closing">Sincerely Your,</p>
    <p class="signature">Your Name</p>
  </main>

  <footer class="contact">
    <div class="contact-row">
      <span class="contact-item">
        <svg viewBox="0 0 12 12"><circle cx="6" cy="6" r="4.5"/><circle cx="6" cy="6" r="1.2" fill="#c8202f"/></svg>
        448 Willowmere Ave, Ste 210, Folsom, CA 95999
      </span>
    </div>
    <div class="contact-row">
      <span class="contact-item">
        <svg viewBox="0 0 12 12"><path d="M3 1.5 L5 4 L4 5.5 Q5 7.5 6.5 8 L8 7 L10.5 9 L9 10.5 Q4 10 1.5 3 Z"/></svg>
        916-555-0187
      </span>
      <span class="contact-item">
        <svg viewBox="0 0 12 12"><rect x="1.5" y="3" width="9" height="6.5"/><path d="M1.5 3 L6 6.5 L10.5 3"/></svg>
        info@brightfieldventures.example
      </span>
      <span class="contact-item">
        <svg viewBox="0 0 12 12"><circle cx="6" cy="6" r="4.5"/><path d="M1.5 6 H10.5 M6 1.5 Q3.5 6 6 10.5 M6 1.5 Q8.5 6 6 10.5"/></svg>
        www.brightfieldventures.example
      </span>
    </div>
  </footer>
</div>
</body>
</html>
```